Website Design for The Elder Nook

Please design and code a new website.
Here are the sites I like best:
http://www.voyaglint.com/alternate/
http://www.wheelgiftbay.org
Please make it similar but look at the competitor site (below) for images and wording. This is NOT a car donation site. It's a senior lead placement site like https://www.kinhavenfinder.com. I just like this sites above as a lead generation sites.
Competitor site:
https://www.kinhavenfinder.com (use ideas / verbiage from this site)
Updates
Competitor site:
Coding
Coded - Design and coding required
Number of Pages Required
1 page
Look and feel
Each slider illustrates characteristics of the customer's brand and the style your logo design should communicate.

```html
<!DOCTYPE html>
<html lang="en">
<head>
<meta charset="utf-8">
<title>The Elder Nook – Senior Living Advisors</title>
<link href="https://fonts.googleapis.com/css2?family=Lora:ital,wght@0,400;0,700;1,400;1,700&family=Open+Sans:wght@400;600;700&display=swap" rel="stylesheet">
<style>
:root{
  --navy:#1b2c48;
  --navy-deep:#13203a;
  --green:#7cc242;
  --green-dark:#5fa42b;
  --ink:#2a3342;
  --muted:#6b7380;
  --line:#e3e6ea;
  --bg-soft:#f5f6f8;
  --white:#fff;
}
*{box-sizing:border-box;margin:0;padding:0}
html,body{width:1200px;height:3276px;overflow:hidden}
body{font-family:"Open Sans",Arial,sans-serif;color:var(--ink);background:var(--white);position:relative}
.serif{font-family:"Lora",Georgia,serif}
section,header,footer,nav{position:absolute;left:0;width:1200px}

/* header */
.site-header{top:0;height:112px;background:var(--white)}
.brand{position:absolute;left:140px;top:34px;display:flex;align-items:center;gap:12px;font-family:"Lora",Georgia,serif;font-weight:700;font-size:30px;color:var(--navy)}
.brand-dot{width:26px;height:26px;border-radius:50%;background:var(--green)}
.header-call{position:absolute;right:140px;top:28px;text-align:right}
.header-call small{display:block;font-size:12px;color:var(--muted)}
.header-call strong{font-size:26px;color:var(--navy)}

.main-nav{top:112px;height:40px;background:var(--navy);display:flex;justify-content:center}
.main-nav a{color:#fff;text-decoration:none;font-size:13px;font-weight:600;letter-spacing:.5px;padding:0 22px;line-height:40px}
.main-nav a.active{background:var(--green)}

/* hero */
.hero{top:152px;height:480px;background:linear-gradient(90deg,#eef0f2 0%,#e4e6e8 45%,#c9c2b8 70%,#a89b8e 100%)}
.hero-photo{position:absolute;right:0;top:0;width:640px;height:480px;background:linear-gradient(135deg,#d8d1c6,#b7a898 55%,#8e8073)}
.hero-copy{position:absolute;left:140px;top:66px;width:440px}
.hero-copy h1{font-family:"Lora",Georgia,serif;font-size:38px;line-height:1.2;color:var(--navy);font-weight:700}
.hero-copy h1 em{color:var(--green);font-weight:700}
.hero-copy .lead{margin-top:12px;font-size:17px;color:var(--ink)}
.field{display:block;width:300px;height:44px;border:1px solid #ccd;background:#fff;font-size:13px;color:#8a909a;padding:0 14px;line-height:44px;margin-top:10px}
.btn{display:inline-block;background:var(--green);color:#fff;font-weight:700;text-align:center;border-radius:3px}
.hero-copy .btn{width:300px;height:50px;line-height:50px;font-size:20px;font-family:"Lora",Georgia,serif;margin-top:10px}
.hero-copy .help{margin-top:10px;font-size:15px;color:var(--navy);font-weight:600}
.badge{width:96px;height:48px;background:var(--navy);margin-top:12px;border-radius:3px}

/* support */
.support{top:632px;height:568px}
.support-photo{position:absolute;left:140px;top:100px;width:430px;height:300px;background:linear-gradient(180deg,#a9cde8 0%,#cfe0ea 50%,#c7b49c 100%)}
.support-copy{position:absolute;left:612px;top:96px;width:448px}
.support-copy h2{font-family:"Lora",Georgia,serif;font-size:30px;line-height:1.25;color:var(--navy);font-weight:400}
.support-copy h2 em{color:var(--green);font-weight:700}
.support-copy p{font-size:12px;color:var(--muted);margin-top:10px;line-height:1.5}
.checklist{list-style:none;margin-top:14px}
.checklist li{display:flex;align-items:center;gap:14px;font-size:13px;color:var(--ink);height:40px}
.checklist svg{flex:none}

/* no cost */
.no-cost{top:1200px;height:280px}
.cost-box{position:absolute;left:280px;top:0;width:780px;height:176px;background:#fff;box-shadow:0 4px 18px rgba(0,0,0,.14);border-left:4px solid var(--green);text-align:center;padding-top:26px}
.cost-box h3{font-family:"Lora",Georgia,serif;font-style:italic;font-size:28px;color:var(--navy)}
.cost-box p{font-size:13px;color:var(--muted);margin-top:10px}
.cost-box .call{font-size:28px;font-weight:700;color:var(--green);margin-top:10px}
.cost-box .call span{color:var(--navy)}

/* advisor */
.advisor{top:1480px;height:500px;background:linear-gradient(90deg,#2a3546 0%,#1c2636 45%,#2b3444 100%)}
.advisor-photo{position:absolute;left:140px;top:40px;width:300px;height:460px;background:linear-gradient(180deg,#3c4556,#232b39)}
.advisor-card{position:absolute;left:440px;top:50px;width:620px;height:380px;background:#fff;text-align:center;padding:34px 40px}
.advisor-card h2{font-family:"Lora",Georgia,serif;font-style:italic;font-size:30px;color:var(--navy);font-weight:400}
.advisor-card h2 em{color:var(--green);font-weight:700}
.advisor-card > p{font-size:12px;color:var(--muted);margin-top:10px}
.perks{display:flex;justify-content:space-between;margin-top:28px}
.perk{width:160px;font-size:11px;color:var(--muted);line-height:1.4}
.perk svg{display:block;margin:0 auto 10px}
.search-row{display:flex;justify-content:center;gap:10px;margin-top:34px}
.search-row .field{margin:0;width:240px;height:40px;line-height:40px;text-align:left}
.search-row .btn{width:200px;height:40px;line-height:40px;font-size:13px}

/* testimonials */
.reviews{top:1980px;height:440px}
.reviews h2{position:absolute;top:92px;width:1200px;text-align:center;font-family:"Lora",Georgia,serif;font-size:30px;color:var(--navy);font-weight:400}
.reviews h2 em{color:var(--green);font-weight:700}
.review{position:absolute;top:170px;width:440px;height:180px;background:#fff;box-shadow:0 3px 14px rgba(0,0,0,.12);padding:24px 28px}
.review-1{left:140px}.review-2{left:620px}
.reviewer{display:flex;align-items:center;gap:14px}
.avatar{width:48px;height:48px;border-radius:50%;background:linear-gradient(135deg,#d6c4b2,#a99585)}
.reviewer strong{display:block;font-family:"Lora",Georgia,serif;font-size:16px;color:var(--navy)}
.stars{color:#f2b01e;font-size:13px;letter-spacing:2px}
.review p{font-size:12px;color:var(--muted);line-height:1.55;margin-top:14px}
.arrow{position:absolute;top:248px}
.arrow-l{left:88px}.arrow-r{right:88px}

/* veterans */
.veterans{top:2420px;height:252px;background:linear-gradient(90deg,#1d3058 0%,#24386a 40%,#3a2f4e 75%,#5a2a36 100%);text-align:center;color:#fff;padding-top:48px}
.veterans h2{font-family:"Lora",Georgia,serif;font-style:italic;font-size:34px;font-weight:700}
.veterans h2 em{color:var(--green)}
.veterans p{width:820px;margin:14px auto 0;font-size:13px;line-height:1.55;color:#d8deea}
.veterans .btn{width:120px;height:34px;line-height:34px;font-size:13px;margin-top:16px}

/* states */
.states{top:2672px;height:488px}
.states h2{position:absolute;top:80px;width:1200px;text-align:center;font-family:"Lora",Georgia,serif;font-size:30px;color:var(--navy);font-weight:400}
.states h2 em{color:var(--green);font-weight:700}
.state-grid{position:absolute;left:150px;top:150px;width:900px;display:flex;justify-content:space-between}
.state-grid ul{list-style:none;width:140px}
.state-grid li{font-size:12.5px;color:var(--ink);line-height:26px;position:relative;padding-left:12px}
.state-grid li::before{content:"";position:absolute;left:0;top:11px;width:4px;height:4px;background:var(--green)}

/* footer */
.footer-nav{top:3160px;height:80px;background:var(--navy);display:flex;justify-content:center;align-items:center}
.footer-nav a{color:#fff;text-decoration:none;font-size:13px;font-weight:600;padding:0 22px}
.footer-bar{top:3240px;height:36px;background:var(--navy-deep);color:#aeb6c4;font-size:11px}
.footer-bar .copy{position:absolute;left:140px;line-height:36px}
.socials{position:absolute;right:140px;top:8px;display:flex;gap:8px}
.socials span{width:20px;height:20px;border-radius:50%;background:#fff;opacity:.85}
</style>
</head>
<body>

<header class="site-header">
  <div class="brand"><span class="brand-dot"></span>The Elder Nook</div>
  <div class="header-call"><small>Call us today for free advice</small><strong>(555) 014 7290</strong></div>
</header>

<nav class="main-nav">
  <a class="active">ASSISTED LIVING</a><a>MEMORY CARE</a><a>NURSING HOMES</a><a>MORE LIVING OPTIONS ▾</a><a>PLANNING &amp; ADVICE</a><a>HOW OUR SERVICE WORKS</a>
</nav>

<section class="hero">
  <div class="hero-photo" role="img" aria-label="Photo of a smiling senior couple embracing"></div>
  <div class="hero-copy">
    <h1>You know your family.<br>We know <em>Senior Living.</em></h1>
    <p class="lead">Find Senior Living Near You</p>
    <span class="field">Enter city or postal code</span>
    <span class="btn">Start Your Search</span>
    <p class="help">Need help? Call (555) 014-7290</p>
    <div class="badge" role="img" aria-label="Accreditation badge"></div>
  </div>
</section>

<section class="support">
  <div class="support-photo" role="img" aria-label="Photo of happy seniors cheering outdoors"></div>
  <div class="support-copy">
    <h2>The support you need to make the <em>Right Choice</em></h2>
    <p>Our local advisors help families compare communities, costs and care levels so every decision feels clear, calm and well informed from the first call.</p>
    <ul class="checklist">
      <li><svg width="28" height="28"><circle cx="14" cy="14" r="14" fill="#1b2c48"/><path d="M9 14l3 3 7-7" stroke="#fff" stroke-width="2" fill="none"/></svg>Dedicated local advisor</li>
      <li><svg width="28" height="28"><circle cx="14" cy="14" r="14" fill="#1b2c48"/><path d="M9 14l3 3 7-7" stroke="#fff" stroke-width="2" fill="none"/></svg>Hand-picked list of communities to match your needs</li>
      <li><svg width="28" height="28"><circle cx="14" cy="14" r="14" fill="#1b2c48"/><path d="M9 14l3 3 7-7" stroke="#fff" stroke-width="2" fill="none"/></svg>Full details &amp; pricing</li>
      <li><svg width="28" height="28"><circle cx="14" cy="14" r="14" fill="#1b2c48"/><path d="M9 14l3 3 7-7" stroke="#fff" stroke-width="2" fill="none"/></svg>Help scheduling tours</li>
      <li><svg width="28" height="28"><circle cx="14" cy="14" r="14" fill="#1b2c48"/><path d="M9 14l3 3 7-7" stroke="#fff" stroke-width="2" fill="none"/></svg>Move-in support</li>
    </ul>
  </div>
</section>

<section class="no-cost">
  <div class="cost-box">
    <h3>There’s No Cost To You</h3>
    <p>We work with over 20,000 senior living communities. Our community partners pay us for placement services.</p>
    <p class="call"><span>CALL</span> 555 018 3340</p>
  </div>
</section>

<section class="advisor">
  <div class="advisor-photo" role="img" aria-label="Photo of a friendly senior living advisor in a suit"></div>
  <div class="advisor-card">
    <h2>Your <em>Local Advisor</em> Informs. You Decide.</h2>
    <p>Over 400 senior advisors across the country help families find the right fit every day.</p>
    <div class="perks">
      <div class="perk"><svg width="36" height="36" viewBox="0 0 36 36"><path d="M18 4a10 10 0 0 0-10 10c0 8 10 18 10 18s10-10 10-18A10 10 0 0 0 18 4z" fill="none" stroke="#7cc242" stroke-width="2"/><circle cx="18" cy="14" r="3.5" fill="#7cc242"/></svg>Insider tips for the area near you</div>
      <div class="perk"><svg width="36" height="36" viewBox="0 0 36 36"><path d="M18 30S5 22 5 13a6.5 6.5 0 0 1 13-2 6.5 6.5 0 0 1 13 2c0 9-13 17-13 17z" fill="none" stroke="#7cc242" stroke-width="2"/></svg>Advice tailored to your unique situation</div>
      <div class="perk"><svg width="36" height="36" viewBox="0 0 36 36"><g stroke="#7cc242" stroke-width="2"><path d="M14 9h18M14 18h18M14 27h18"/><circle cx="7" cy="9" r="2" fill="#7cc242"/><circle cx="7" cy="18" r="2" fill="#7cc242"/><circle cx="7" cy="27" r="2" fill="#7cc242"/></g></svg>Time saving tours from trusted homes</div>
    </div>
    <div class="search-row"><span class="field">Enter city or postal code</span><span class="btn">Find an Advisor Near You</span></div>
  </div>
</section>

<section class="reviews">
  <h2>93% Of Our <em>Customers Recommend</em> Our Service</h2>
  <svg class="arrow arrow-l" width="20" height="32"><path d="M16 2L4 16l12 14" stroke="#1b2c48" stroke-width="2.5" fill="none"/></svg>
  <div class="review review-1">
    <div class="reviewer"><span class="avatar"></span><div><strong>Marla Dunfield</strong><span class="stars">★★★★★</span></div></div>
    <p>Our advisor listened closely and found a lovely community for my mother within a week. Every question was answered with patience, and the tours were easy to plan around our busy family schedule.</p>
  </div>
  <div class="review review-2">
    <div class="reviewer"><span class="avatar"></span><div><strong>Owen Pritchard</strong><span class="stars">★★★★★</span></div></div>
    <p>We had no idea where to start until we called. The options matched our budget, the pricing was clear, and the move-in help made a hard season much lighter for my dad and for all of us.</p>
  </div>
  <svg class="arrow arrow-r" width="20" height="32"><path d="M4 2l12 14L4 30" stroke="#1b2c48" stroke-width="2.5" fill="none"/></svg>
</section>

<section class="veterans">
  <h2>Access Up To <em>$2,000 Per Month</em> In Veteran’s Aid</h2>
  <p>We work with veterans every day. Most veteran families do not know of a key benefit available to them and their families. It’s called the Veteran’s Aid &amp; Attendance benefit. This benefit can help pay for senior living and home care.</p>
  <span class="btn">Learn More</span>
</section>

<section class="states">
  <h2>Senior Assisted <em>Living by State</em></h2>
  <div class="state-grid">
    <ul><li>Alabama</li><li>Alaska</li><li>Arizona</li><li>Arkansas</li><li>California</li><li>Colorado</li><li>Connecticut</li><li>Delaware</li></ul>
    <ul><li>District of Columbia</li><li>Florida</li><li>Georgia</li><li>Hawaii</li><li>Idaho</li><li>Illinois</li><li>Indiana</li></ul>
    <ul><li>Iowa</li><li>Kansas</li><li>Kentucky</li><li>Louisiana</li><li>Maine</li><li>Maryland</li><li>Massachusetts</li></ul>
    <ul><li>Michigan</li><li>Minnesota</li><li>Mississippi</li><li>Missouri</li><li>Montana</li><li>Nebraska</li><li>Nevada</li></ul>
    <ul><li>New Hampshire</li><li>New Jersey</li><li>New Mexico</li><li>New York</li><li>North Carolina</li><li>North Dakota</li><li>Ohio</li></ul>
    <ul><li>Oklahoma</li><li>Oregon</li><li>Pennsylvania</li><li>Rhode Island</li><li>South Carolina</li><li>South Dakota</li><li>Tennessee</li></ul>
  </div>
</section>

<nav class="footer-nav">
  <a>ASSISTED LIVING</a><a>MEMORY CARE</a><a>NURSING HOMES</a><a>MORE LIVING OPTIONS ▾</a><a>PLANNING &amp; ADVICE</a><a>HOW OUR SERVICE WORKS</a>
</nav>
<footer class="footer-bar">
  <span class="copy">Copyright © The Elder Nook. All Rights Reserved.</span>
  <div class="socials"><span></span><span></span><span></span><span></span></div>
</footer>

</body>
</html>
```